Using attached logo that has been created

Business card with logo that's attached. Maybe with water or the cartoon van in background. Looking for it to not be so plain and not too white.
Information to include;
Rodney Ashcombe
(555) 218-7730
Info@bramleypipeworks.example
www.bramleypipeworks.example
License # 4627195
Looking forward to the designs u come up with.
Thank you!
-Delphine
Target Market(s)
Plumbing
Industry/Entity Type
Plumbing
Contact Information for Business Card
Listed above

```html
<!DOCTYPE html>
<html lang="en">
<head>
<meta charset="utf-8">
<title>Bramley Pipeworks – Business Card</title>
<link rel="stylesheet" href="https://fonts.googleapis.com/css2?family=Alfa+Slab+One&family=Arvo:wght@400;700&display=swap">
<style>
  :root {
    --page: #d9d9db;
    --card-blue: #0a4ea8;
    --card-yellow: #fdba00;
    --accent-yellow: #f7b800;
    --ink-white: #ffffff;
    --ink-dark: #1a1a1a;
    --logo-blue: #0b4aa6;
    --art-blue: #1d5fc4;
    --art-tan: #9a7a52;
  }
  * { box-sizing: border-box; margin: 0; padding: 0; }
  html, body { width: 1200px; height: 800px; overflow: hidden; }
  body {
    background: var(--page);
    display: flex;
    align-items: center;
    justify-content: center;
    gap: 40px;
  }
  .card {
    position: relative;
    width: 540px;
    height: 310px;
    border-radius: 22px;
    overflow: hidden;
  }
  /* Back side: contact details */
  .card--contact { background: var(--card-blue); }
  .mascot-art {
    position: absolute;
    right: 20px;
    top: 20px;
    width: 250px;
    height: 290px;
    border-radius: 120px 120px 0 0;
    background: linear-gradient(180deg, var(--art-blue) 0%, #2a6ad0 55%, var(--art-tan) 100%);
  }
  .contact-block {
    position: absolute;
    left: 34px;
    bottom: 34px;
    color: var(--ink-white);
    font-family: "Arvo", serif;
  }
  .holder-name {
    font-family: "Alfa Slab One", serif;
    font-size: 27px;
    letter-spacing: 0.5px;
    color: var(--accent-yellow);
    text-transform: uppercase;
    line-height: 1;
  }
  .rule {
    width: 70px;
    height: 1px;
    background: var(--ink-white);
    margin: 14px 0 10px;
  }
  .contact-list { list-style: none; }
  .contact-list li {
    display: flex;
    align-items: center;
    gap: 10px;
    font-size: 14px;
    line-height: 1.45;
  }
  .contact-list svg { width: 13px; height: 13px; flex: none; }
  .license { font-size: 15px; }

  /* Front side: logo */
  .card--brand { background: var(--card-yellow); }
  .brand-art {
    position: absolute;
    left: 50%;
    top: 36px;
    transform: translateX(-50%);
    width: 110px;
    height: 150px;
    border-radius: 50px 50px 10px 10px;
    background: linear-gradient(180deg, var(--art-blue) 0%, #2a62c0 50%, var(--art-tan) 100%);
  }
  .brand-name {
    position: absolute;
    left: 0; right: 0;
    top: 196px;
    text-align: center;
    font-family: "Arvo", serif;
    font-weight: 700;
    font-size: 26px;
    color: var(--logo-blue);
    line-height: 1;
  }
  .brand-web {
    position: absolute;
    left: 0; right: 0;
    bottom: 34px;
    text-align: center;
    font-family: "Arvo", serif;
    font-size: 13px;
    letter-spacing: 5px;
    color: var(--ink-dark);
    text-transform: uppercase;
  }
</style>
</head>
<body>
  <section class="card card--contact">
    <div class="mascot-art" role="img" aria-label="Cartoon plumber mascot in a blue shirt holding a pipe wrench and a circular saw"></div>
    <div class="contact-block">
      <h1 class="holder-name">Rodney Ashcombe</h1>
      <div class="rule"></div>
      <ul class="contact-list">
        <li>
          <svg viewBox="0 0 24 24" fill="var(--accent-yellow)"><path d="M6.6 10.8a15.1 15.1 0 0 0 6.6 6.6l2.2-2.2a1 1 0 0 1 1-.25 11.4 11.4 0 0 0 3.6.57 1 1 0 0 1 1 1V20a1 1 0 0 1-1 1A17 17 0 0 1 3 4a1 1 0 0 1 1-1h3.5a1 1 0 0 1 1 1c0 1.25.2 2.45.57 3.57a1 1 0 0 1-.25 1z"/></svg>
          (555) 218-7730
        </li>
        <li>
          <svg viewBox="0 0 24 24" fill="var(--accent-yellow)"><path d="M2 5h20v14H2z"/><path d="M2 5l10 8 10-8" fill="none" stroke="var(--card-blue)" stroke-width="2"/></svg>
          Info@bramleypipeworks.example
        </li>
        <li>
          <svg viewBox="0 0 24 24"><circle cx="12" cy="12" r="10" fill="var(--accent-yellow)"/><path d="M2 12h20M12 2c3 3 3 17 0 20M12 2c-3 3-3 17 0 20" fill="none" stroke="var(--card-blue)" stroke-width="1.6"/></svg>
          bramleypipeworks.example
        </li>
      </ul>
      <div class="rule"></div>
      <p class="license">License # 4627195</p>
    </div>
  </section>

  <section class="card card--brand">
    <div class="brand-art" role="img" aria-label="Cartoon plumber mascot holding a pipe wrench and a circular saw"></div>
    <p class="brand-name">Bramley Pipeworks &amp; More</p>
    <p class="brand-web">www.bramleypipeworks.example</p>
  </section>
</body>
</html>
```